Wordpress website design for a Herbal Health Care Company

** Outcome of this project is only the design. Only PSD files of the design for unique pages are sufficient.
** There are a number of unique pages in the new site as shown in the wire-frame. However, for the selection of the designer, Homepage, one 2nd tier page (product category) and one 3rd tier page (product page) is sufficient.
We need web design for our for Ayurvedic & Herbal Products Company located in Sri Lanka
Please get the idea about our company by reading the following text
Vision : To be a world class manufacturer and a supplier of highest quality Ayurvedic pharmaceuticals, Herbal health care products, Herbal cosmetics, Essential oils and Oleoresins
Mission : To provide safe and effective Ayurvedic pharmaceuticals, Herbal health care products and Herbal cosmetics, that is of highest quality and integrity, through the incorporation of ancient ayurvedic wisdom with modern technology and scientific management systems for the inprovement of health and longevity of the people.
Policy on Quality : To design, develop, produce and deliver safe, efficacious and consistent quality Herbal health care products based on Ancient Ayurvedic Wisdom using environmentally preferred process technologies and competent personnel towards continual commitment to total customer satisfaction.
(1) Color theme of the website
You can use the color derived from the company logo
(2) Site Map and description of the site
(1) Home
see the wire frame
http://clipmora.net/t/qWxPlKmR4s7T
we need drop-down menu for top menu bar
(2) About Fern Vale [ This is single page with some description + imaged and following sub page links should be placed in this page]
2.1 Board of Directors
2.2 Milestones
2.3 Our Logo
2.4 Production & R&D
2.5 Certification and Awards
2.6 Global Presence
2.7 Investors
2.8 Distribution
(3)Ayurveda Pharmaceuticals [ This is one of the 3 main categories ,Category Main Page should provide an introduction to the category]
Following shows the sub categories of the “Ayurvedic Pharmaceuticals” . each subcategory has different products. We need unique design for Main Category Page and Sub category
3.1 Arista
3.2 Asava
3.3 Coorna
3.4 Lepa
3.5 Gritha
3.7 Guggulu
3.8 Kalka
3.9 Kwatha
3.10 Pana
see the wireframe
http://clipmora.net/t/7KrtVm83BQNN
when you click subcategory , we nee a page like this to list products
http://clipmora.net/t/HXwQ5nDe21
(4) Herbal Health Care Products [ This is one of the 3 main categories]
you do not find subcategories, you have only products listed. we need unique design for this category page + products
This page will consists of category description with image and products listed
see the wire frame
(5) Cosmetics & Spa Products
see the wire frame
(6) Essential Oils & Oleoresins
see the wire frame
(7) Media
We need to put video / image gallery / text . and future events
(8) Investors
related information to investors
we need image + text
(9) CSR
(10) Contact US
contact us form / address / telephone number and google map
(11) Log In
Normal login form
(12) Career
Reference Details
http://clipmora.net/t/9PeLcR4TYJ
http://clipmora.net/t/5MgkDRR2Vu
http://clipmora.net/t/bNqVrTHww
Here is a similar site that should give you some idea how we like the new site to look http://www.velkor.com
Industry/Entity Type
Health Care
Requirements
Must have
- We have 4 main categories in our production line
Quality Ayurvedic pharmaceuticals, Herbal health care products, Herbal cosmetics, Essential oils and Oleoresins
You can use 4 boxes below the slider for it ( This very important to have unique different design for each category with some heading, text and images etc)
Nice to have
- You can suggest any good nice features. Try to keep a clean, natural, relaxing theme, with shades of green, white and orange as per their logo. This can be seen from the project brief attachments. www.velkor.com is an example.
Should not have
- Please avoid dark colours (red) and sad colours (grey, black)

```html
<!DOCTYPE html>
<html lang="en">
<head>
<meta charset="utf-8">
<title>Fern Vale – Ayurvedic Pharmaceuticals</title>
<link href="https://fonts.googleapis.com/css2?family=Arimo:ital,wght@0,400;0,700;1,700&family=Didact+Gothic&display=swap" rel="stylesheet">
<style>
:root{
  --green-dark:#2f7d12;
  --green:#3f9a1c;
  --green-light:#5fb82c;
  --grass:#4aa51f;
  --panel:#f6fbea;
  --panel-line:#d9e8c3;
  --orange:#d8481b;
  --orange-dark:#b33410;
  --text:#555;
  --heading:#2b2b2b;
  --white:#fff;
  --grey-band:#e9e9e9;
}
*{margin:0;padding:0;box-sizing:border-box}
html,body{width:871px;height:1200px;overflow:hidden;background:var(--white)}
body{position:relative;font-family:"Arimo",Arial,sans-serif;color:var(--text)}
.abs{position:absolute}

/* header */
.site-header{left:0;top:0;width:871px;height:120px;
  background:linear-gradient(180deg,var(--green-dark) 0%,var(--green) 60%,var(--grass) 85%,#7cc44a 100%)}
.brand{left:32px;top:21px;width:84px;height:53px;background:var(--white);border-radius:3px;
  display:flex;align-items:center;justify-content:center;gap:5px}
.brand-dot{width:9px;height:9px;border-radius:50%;background:var(--orange)}
.brand-name{font-family:"Didact Gothic",sans-serif;font-size:15px;color:var(--green)}
.tagline{left:133px;top:39px;font-style:italic;font-weight:700;font-size:18px;color:var(--white)}
.top-links{right:8px;top:15px;display:flex;gap:14px;font-size:10px;font-weight:700;color:var(--white)}
.search{left:753px;top:45px;width:113px;height:16px;background:#eef3ea;border-radius:8px;
  font-size:8px;color:#777;padding:3px 8px}
.search svg{position:absolute;right:5px;top:3px}

/* nav */
.main-nav{left:196px;top:127px;height:36px;display:flex;border:1px solid #e3e3e3;background:var(--white)}
.main-nav a{font-family:"Didact Gothic",sans-serif;font-size:11px;color:#444;text-decoration:none;
  padding:6px 13px 0;border-right:1px solid #e3e3e3;line-height:1.1}
.main-nav a small{display:block;font-size:7px;color:#777}
.main-nav a.active{color:var(--orange)}
.main-nav a.active small{color:var(--orange)}
.main-nav a.plain{padding-top:12px}

/* slider */
.slider-band{left:0;top:165px;width:871px;height:197px;background:var(--grey-band)}
.slide-side-left{left:0;top:182px;width:142px;height:162px;background:linear-gradient(120deg,#e53d63,#f5a1b4 60%,#c23b55)}
.slide-side-right{left:729px;top:182px;width:142px;height:162px;background:linear-gradient(120deg,#cfe8e4,#8fbf7a 60%,#e7f0ea)}
.slide-main{left:142px;top:165px;width:587px;height:194px;
  background:linear-gradient(90deg,#a79aae 0%,#7a6a72 30%,#3b2a22 55%,#4d3a2c 80%,#2e211a 100%);
  box-shadow:0 4px 10px rgba(0,0,0,.25)}
.slide-tab{left:316px;top:340px;width:242px;height:24px;border-radius:4px 4px 0 0;
  background:linear-gradient(180deg,var(--orange),var(--orange-dark))}
.dots{left:470px;top:348px;display:flex;gap:3px}
.dots span{width:8px;height:8px;border-radius:50%;border:1px solid #f7c1a9}
.dots span.on{background:var(--white)}

/* breadcrumb */
.breadcrumb{left:156px;top:385px;font-size:10px;color:#444;display:flex;gap:6px;align-items:center}

/* content panel */
.panel{left:149px;top:408px;width:574px;height:600px;border:1px solid var(--panel-line);
  border-radius:4px;background:var(--white)}
.panel-intro{left:149px;top:408px;width:574px;height:190px;background:var(--panel);border-radius:4px 4px 0 0}
.page-title{left:158px;top:422px;font-family:"Didact Gothic",sans-serif;font-size:20px;color:var(--heading)}
.intro{left:158px;width:556px;font-size:7.6px;line-height:11px;color:#666;text-align:justify}
.product-title{left:156px;width:558px;font-family:"Didact Gothic",sans-serif;font-size:14px;color:#333;
  border-bottom:1px solid #e2e2e2;padding-bottom:4px}
.product-photo{left:156px;width:210px;height:156px;
  background:radial-gradient(circle at 40% 60%,#9c6b3a 0%,#7aa83e 35%,#cfe7a1 65%,var(--white) 80%)}
.product-text{left:366px;width:348px;font-size:7.6px;line-height:11px;color:#666}
.btn-more{left:367px;width:57px;height:16px;border-radius:3px;background:linear-gradient(180deg,var(--orange),var(--orange-dark));
  color:var(--white);font-size:7px;text-align:center;line-height:16px}

/* footer */
.site-footer{left:0;top:1029px;width:871px;height:171px;background:linear-gradient(180deg,var(--grass),var(--green-dark))}
.footer-heading{font-family:"Didact Gothic",sans-serif;font-size:14px;color:var(--white);top:1056px}
.footer-rule{top:1078px;height:1px;background:rgba(255,255,255,.5)}
.social{top:1086px;width:14px;height:14px;border-radius:3px;background:#3aa1d8}
.social.alt{background:#3b5ea8}
.blog{left:351px;top:1100px;font-size:8px;line-height:13px;color:#b81e0c;font-weight:700}
.blog .lead{font-size:7px}
.blog li{list-style:none;color:#c21d0a}
.blog li::before{content:"●";color:var(--white);margin-right:5px}
.contact{left:549px;top:1089px;font-size:7px;line-height:11px;color:var(--white)}
.contact b{font-weight:700}
.legal{left:0;top:1164px;width:871px;text-align:center;font-size:7px;color:#e4f2d8}
</style>
</head>
<body>

<header class="site-header abs">
</header>
<div class="brand abs"><span class="brand-dot"></span><span class="brand-name">Fern Vale</span></div>
<div class="tagline abs">“ .. A Healthy Long Life ”</div>
<nav class="top-links abs"><span>Media</span><span>Investors</span><span>Careers</span><span>CSR</span><span>Contact Us</span><span>Log In</span></nav>
<div class="search abs">Search...
  <svg width="10" height="10" viewBox="0 0 10 10"><circle cx="4" cy="4" r="3" fill="none" stroke="#666" stroke-width="1.3"/><line x1="6.3" y1="6.3" x2="9" y2="9" stroke="#666" stroke-width="1.5"/></svg>
</div>

<nav class="main-nav abs">
  <a class="plain">Home</a>
  <a class="plain">About Fern Vale</a>
  <a class="active">Ayurvedic<small>Pharmaceuticals</small></a>
  <a>Herbal Health<small>Care Products</small></a>
  <a>Cosmetics, Aroma<small>&amp; Spa Products</small></a>
  <a>Essential Oils<small>&amp; Oleoresins</small></a>
</nav>

<div class="slider-band abs"></div>
<div class="slide-side-left abs" role="img" aria-label="Pink lily flower photograph"></div>
<div class="slide-side-right abs" role="img" aria-label="Glass bottle of herbal oil with green leaves"></div>
<div class="slide-main abs" role="img" aria-label="Bowls of dried lavender, peppercorns and spices"></div>
<div class="slide-tab abs"></div>
<div class="dots abs"><span class="on"></span><span></span><span></span><span></span><span></span></div>

<div class="breadcrumb abs">
  <svg width="10" height="10" viewBox="0 0 10 10"><path d="M1 5 L5 1 L9 5 M2.5 4 V9 H7.5 V4" fill="none" stroke="#999" stroke-width="1.2"/></svg>
  Ayurvedic
</div>

<main>
  <div class="panel abs"></div>
  <div class="panel-intro abs"></div>
  <h1 class="page-title abs">Ayurvedic Pharmaceuticals</h1>
  <p class="intro abs" style="top:453px">Our Ayurvedic range brings together remedies prepared from roots, barks, leaves and seeds gathered from trusted growers across the island. Each formula follows classical texts and is made in small batches under careful quality checks. We blend ancient methods of decoction, fermentation and slow cooking with modern testing so that every bottle, powder and paste is safe, steady and true to its tradition. Our pharmacists and physicians work side by side to choose the best herbs, measure each dose with care and keep the natural strength of every plant intact from field to shelf for your family.</p>
  <p class="intro abs" style="top:525px">Browse the groups below to find arishta, asava, churna, lepa, ghrita and other classical preparations. Every product page lists its herbs, its uses and the right way to take it. If you are unsure which remedy suits you, our team of qualified physicians is happy to guide you and answer your questions by phone or email at any time.</p>

  <article>
    <h2 class="product-title abs" style="top:620px">Product 01</h2>
    <div class="product-photo abs" style="top:649px" role="img" aria-label="Herbs in a wooden mortar with lemon and an amber oil bottle"></div>
    <p class="product-text abs" style="top:651px">A gentle herbal tonic made from fresh leaves, roots and citrus peel, slowly brewed to support digestion and daily strength. Take two spoons after meals with warm water. Suitable for adults and children over twelve years of age.</p>
    <div class="btn-more abs" style="top:711px">READ MORE...</div>
  </article>

  <article>
    <h2 class="product-title abs" style="top:818px">Product 02</h2>
    <div class="product-photo abs" style="top:847px" role="img" aria-label="Herbs in a wooden mortar with lemon and an amber oil bottle"></div>
    <p class="product-text abs" style="top:852px">A gentle herbal tonic made from fresh leaves, roots and citrus peel, slowly brewed to support digestion and daily strength. Take two spoons after meals with warm water. Suitable for adults and children over twelve years of age.</p>
    <div class="btn-more abs" style="top:909px">READ MORE...</div>
  </article>
</main>

<footer class="site-footer abs"></footer>
<h3 class="footer-heading abs" style="left:174px">Follow Us</h3>
<div class="footer-rule abs" style="left:160px;width:170px"></div>
<div class="social abs" style="left:158px"></div>
<div class="social alt abs" style="left:176px"></div>

<h3 class="footer-heading abs" style="left:351px">Fern Vale Blog Feeds</h3>
<div class="blog abs">
  <div class="lead">Fern Vale Products Blog</div>
  <ul><li>Green Leaf Awards 2009</li><li>Create, Grow and Share</li></ul>
</div>

<h3 class="footer-heading abs" style="left:549px">
  <svg width="10" height="9" viewBox="0 0 10 9" style="margin-right:4px"><path d="M0 1H10M0 4.5H10M0 8H10" stroke="#fff" stroke-width="1.2"/></svg>Our Contact Details</h3>
<div class="contact abs">
  <div><b>E-mail</b> info@fernvaleherbals.com</div>
  <div><b>Telephone</b> (+00 11) 2460 318/2460 319</div>
  <div><b>Fax</b> (+00 11) 2460 320</div>
</div>

<div class="legal abs">Fern Vale Products © All rights reserved</div>

</body>
</html>
```